Corvane Capital Business Cards

These are professional business cards that are for my family office.
Put fake emails and phone numbers as of now until I finalize those components. This family office controls my families investments, assets, and future. The cards should be professional.
..
.
.
.
I just uploaded another variation of a logo I would like to see as a business card to I am inbeteen which logo to use

Target Market(s)

business

Industry/Entity Type

business

Contact Information for Business Card

Professional, wealth related, finance related.

Requirements
Must have
• Logo

```html
<!DOCTYPE html>
<html lang="en">
<head>
<meta charset="utf-8">
<title>Corvane Capital Business Cards</title>
<link href="https://fonts.googleapis.com/css2?family=Montserrat:wght@400;500;600;800&display=swap" rel="stylesheet">
<style>
  :root {
    --navy: #171c2c;
    --navy-deep: #11151f;
    --ink: #1b2033;
    --white: #ffffff;
    --stage: #e7e5e1;
    --muted: #8a8e99;
  }
  html, body {
    margin: 0;
    padding: 0;
    width: 1200px;
    height: 931px;
    overflow: hidden;
    background: var(--stage);
    font-family: "Montserrat", sans-serif;
  }
  .canvas {
    position: relative;
    width: 1200px;
    height: 931px;
  }
  .card {
    position: absolute;
    width: 640px;
    height: 366px;
    border-radius: 22px;
    box-shadow: 0 14px 30px rgba(0,0,0,0.22);
    overflow: hidden;
  }
  .card-back {
    left: 60px;
    top: 50px;
    background: var(--navy);
  }
  .back-pattern {
    position: absolute;
    inset: 0;
    background: linear-gradient(120deg, #2a3044 0%, var(--navy) 45%, var(--navy-deep) 100%);
  }
  .back-brand {
    position: absolute;
    right: 60px;
    top: 150px;
    display: flex;
    align-items: center;
    gap: 12px;
    color: var(--white);
    font-weight: 600;
    font-size: 20px;
    letter-spacing: 0.04em;
  }
  .brand-dot {
    width: 34px;
    height: 34px;
    border-radius: 50%;
    border: 2px solid currentColor;
    box-sizing: border-box;
  }
  .card-front {
    left: 500px;
    top: 470px;
    background: var(--white);
    color: var(--ink);
  }
  .front-brand {
    position: absolute;
    right: 50px;
    top: 95px;
    display: flex;
    align-items: center;
    gap: 14px;
    font-weight: 600;
    font-size: 24px;
    letter-spacing: 0.05em;
    color: var(--ink);
  }
  .front-brand .brand-dot {
    width: 46px;
    height: 46px;
    border-width: 3px;
  }
  .rule-main {
    position: absolute;
    left: 40px;
    right: 40px;
    top: 178px;
    height: 2px;
    background: var(--ink);
  }
  .address {
    position: absolute;
    right: 50px;
    top: 192px;
    text-align: right;
    font-size: 13px;
    line-height: 1.45;
    font-weight: 500;
  }
  .person {
    position: absolute;
    left: 40px;
    top: 200px;
  }
  .person-name {
    margin: 0;
    font-weight: 800;
    font-size: 28px;
    line-height: 1.1;
  }
  .person-role {
    margin: 2px 0 0;
    font-size: 15px;
    font-weight: 400;
  }
  .rule-person {
    width: 250px;
    height: 2px;
    background: var(--ink);
    margin: 8px 0 8px;
  }
  .contacts {
    list-style: none;
    margin: 0;
    padding: 0;
    font-size: 14px;
    line-height: 1.6;
  }
  .contacts li {
    display: flex;
    align-items: center;
    gap: 10px;
  }
  .contacts svg {
    width: 14px;
    height: 14px;
    fill: var(--ink);
    flex: none;
  }
</style>
</head>
<body>
<div class="canvas">

  <section class="card card-back">
    <div class="back-pattern" role="img" aria-label="Repeating tone-on-tone brand pattern on navy"></div>
    <div class="back-brand"><span class="brand-dot"></span>Corvane Capital</div>
  </section>

  <section class="card card-front">
    <div class="front-brand"><span class="brand-dot"></span>Corvane Capital</div>
    <div class="rule-main"></div>
    <div class="address">240 Linden Court Plaza<br>Fairhaven, NJ 07000 USA</div>

    <div class="person">
      <h1 class="person-name">Marcus Delaney</h1>
      <p class="person-role">Owner</p>
      <div class="rule-person"></div>
      <ul class="contacts">
        <li>
          <svg viewBox="0 0 24 24"><path d="M6.6 10.8a15.1 15.1 0 0 0 6.6 6.6l2.2-2.2a1 1 0 0 1 1-.25 11.4 11.4 0 0 0 3.6.57 1 1 0 0 1 1 1V20a1 1 0 0 1-1 1A17 17 0 0 1 3 4a1 1 0 0 1 1-1h3.5a1 1 0 0 1 1 1c0 1.25.2 2.45.57 3.57a1 1 0 0 1-.25 1z"/></svg>
          (555)014-2736
        </li>
        <li>
          <svg viewBox="0 0 24 24"><path d="M2 5h20v14H2z M2 5l10 8 10-8" /></svg>
          info@yourwebsitename.com
        </li>
        <li>
          <svg viewBox="0 0 24 24"><circle cx="12" cy="12" r="10"/><path d="M2 12h20M12 2c3 3 3 17 0 20M12 2c-3 3-3 17 0 20" stroke="#fff" stroke-width="1.5" fill="none"/></svg>
          www.yourwebsitename.com
        </li>
      </ul>
    </div>
  </section>

</div>
</body>
</html>
```